Flyer for Yoga and IronPulse.

Just initial idea and open to creativity: I am thinking right half of flyer to be IronPulse info and left half to be Yoga info.
Feel free to add text as needed but would like following:
Basic text: ZenLoftVo $69/mo unlimited sessions.
ZenLoftVO.com
IronPulse: $99 intro session. Largest IronPulse in Texas.
IronPulseVO.com

Located North Riverside Houston (NRVO)
Address: 4817 Marlow Pkwy Houston, tx

Please submit any and all designs. Looking to get some great ideas!

Target Market(s)

Young professionals free spirited and fun atmosphere.

Colors
3176b5
85acd3
32a6d7
32b7a4
f59195
cde9f5
f04a50

Requirements
Must have
• Professional yet fun. Text should include:
ZenLoftVo and IronPulse Vo taking each a half of the page seperatly get still be identifiable as one. Want to show there is two options for either yoga or IronPulse or do both!
IronPulse Intro is $99 adm yoga intro is $69.
Nice to have
• Also visit www.ironpulsevo.com for more ideas and info.

```html
<!DOCTYPE html>
<html lang="en">
<head>
<meta charset="utf-8">
<title>IronPulse Vo &amp; ZenLoftVo Flyer</title>
<link rel="stylesheet" href="https://fonts.googleapis.com/css2?family=Oswald:wght@400;500;600&family=Open+Sans:wght@400;600&display=swap">
<style>
  :root {
    --red: #c8283a;
    --teal: #2fb8c6;
    --ink: #2b2b2b;
    --grey-line: #5f6166;
    --paper: #ffffff;
    --gym-dark: #4a4642;
    --gym-light: #b9b2a8;
    --sky: #e6eef2;
    --grass: #6f8f3a;
  }
  * { margin: 0; padding: 0; box-sizing: border-box; }
  html, body { width: 825px; height: 1200px; overflow: hidden; background: var(--paper); }
  .flyer { position: relative; width: 825px; height: 1200px; background: var(--paper); font-family: "Open Sans", Arial, sans-serif; color: var(--ink); overflow: hidden; }

  .shapes { position: absolute; inset: 0; }

  .photo { position: absolute; inset: 0; }
  .photo--gym {
    background: linear-gradient(160deg, var(--gym-light) 0%, #8d857c 45%, var(--gym-dark) 100%);
    clip-path: polygon(330px 0, 825px 0, 825px 473px, 330px 557px);
  }
  .photo--yoga {
    background: linear-gradient(180deg, var(--sky) 0%, #cfdcc4 45%, #8fa65a 75%, var(--grass) 100%);
    clip-path: polygon(15px 651px, 493px 562px, 493px 1112px, 15px 1112px);
  }

  .site-url { position: absolute; font-family: "Oswald", Arial Narrow, sans-serif; font-weight: 500; color: var(--paper); letter-spacing: 0.5px; }
  .site-url--gym { left: 45px; top: 40px; font-size: 32px; }
  .site-url--yoga { left: 580px; top: 1040px; font-size: 31px; }

  .brand { position: absolute; display: flex; align-items: center; gap: 10px; font-family: "Oswald", Arial Narrow, sans-serif; font-weight: 600; }
  .brand--gym { left: 60px; top: 180px; font-size: 34px; color: var(--ink); }
  .brand--gym .brand-mark { width: 16px; height: 16px; background: var(--red); }
  .brand--yoga { left: 560px; top: 560px; flex-direction: column; gap: 12px; font-size: 48px; color: var(--red); width: 220px; }
  .brand--yoga .brand-mark { width: 34px; height: 34px; border-radius: 50%; background: var(--teal); }

  .copy { position: absolute; font-size: 15.5px; line-height: 18.5px; color: var(--ink); }
  .copy p + p { margin-top: 18.5px; }
  .copy--gym { left: 45px; top: 292px; width: 285px; }
  .copy--yoga { left: 540px; top: 742px; width: 265px; }

  .tag { position: absolute; font-family: "Oswald", Arial Narrow, sans-serif; font-weight: 500; text-transform: uppercase; display: flex; align-items: center; white-space: nowrap; }
  .tag--intro { left: 431px; top: 305px; width: 357px; height: 60px; background: rgba(255,255,255,0.9); color: var(--red); font-size: 39px; justify-content: center; }
  .tag--largest { left: 330px; top: 372px; width: 495px; height: 67px; background: rgba(255,255,255,0.88); color: var(--ink); font-size: 36px; padding-left: 20px; }
  .tag--price { left: 15px; top: 917px; width: 404px; height: 64px; background: rgba(255,255,255,0.9); color: var(--red); font-size: 38px; padding-left: 18px; }
  .tag--unlimited { left: 15px; top: 995px; width: 374px; height: 52px; background: rgba(255,255,255,0.9); color: var(--teal); font-size: 32px; padding-left: 18px; }

  .footer { position: absolute; left: 0; right: 0; top: 1122px; text-align: center; font-family: "Oswald", Arial Narrow, sans-serif; }
  .footer-call { color: var(--red); font-size: 21px; font-weight: 500; text-transform: uppercase; }
  .footer-address { margin-top: 6px; color: var(--ink); font-size: 15px; font-weight: 400; text-transform: uppercase; }
</style>
</head>
<body>
<main class="flyer">
  <svg class="shapes" width="825" height="1200" viewBox="0 0 825 1200" aria-hidden="true">
    <polygon class="band-red" points="0,0 624,0 0,160" fill="#c8283a"/>
    <line class="divider" x1="0" y1="654" x2="500" y2="561" stroke="#5f6166" stroke-width="6"/>
    <polygon class="band-teal" points="223,1112 825,966 825,1112" fill="#2fb8c6"/>
  </svg>

  <div class="photo photo--gym" role="img" aria-label="Photo of adults training on rowing machines in a gym"></div>
  <div class="photo photo--yoga" role="img" aria-label="Photo of women doing a side-angle yoga pose on grass in a park"></div>

  <div class="site-url site-url--gym">IRONPULSEVO.COM</div>

  <div class="brand brand--gym"><span class="brand-mark"></span><span>IronPulse Vo</span></div>
  <div class="copy copy--gym">
    <p>Visit IronPulse Vo (North Riverside Houston) today for a FREE trial class! $99 IronPulse 101 Intro program. Largest IronPulse in Texas.</p>
    <p>6:00am,10:00am,11:00am, 12:00pm, 4:30pm, 5:30pm, 6:00pm, 6:30pm, 7:00pm, 8:00pm Classes.</p>
    <p>Lots of showers, parking, and fun!</p>
  </div>

  <div class="tag tag--intro">$99 Intro Session</div>
  <div class="tag tag--largest">Largest IronPulse in Texas.</div>

  <div class="brand brand--yoga"><span class="brand-mark"></span><span>ZenLoftVo</span></div>
  <div class="copy copy--yoga">
    <p>Find your passion and center with ZenLoftVo. Located in North Riverside we have all different styles of yoga for you to enjoy.</p>
    <p>Try a FREE class then join for a special rate of $69/mo.</p>
  </div>

  <div class="tag tag--price">ZenLoftVo $69/mo</div>
  <div class="tag tag--unlimited">Unlimited Sessions.</div>

  <div class="site-url site-url--yoga">ZENLOFTVO.COM</div>

  <footer class="footer">
    <div class="footer-call">Visit us today for more information and follow us on SocialSpot!</div>
    <div class="footer-address">Located North Riverside Houston (NRVO) Address: 4817 Marlow Pkwy Houston, TX</div>
  </footer>
</main>
</body>
</html>
```